The hardcover "Azure Lantern" (large size, Quarto 4º, 12 × 9 1/2 in, 30.5 × 24.15 cm) in German language as follows:

AZURNE LATERNE (title)
der bedeutendsten Gründer und Vordenker Norddeutschlands 2016 (subtitle 1)
HAMBURG UND UMLAND (subtitle 2, smaller than subtitle 1)

Brivomark (logo, WMF file attached)

Reason: The solutions are rather too childish and pre-made styles... is there anyone who can make it better? - a professional-looking business book (encyclopedia style, should have no color-pictures, no author's name, logo smaller due to the large size book)

Target Market(s)

business community

Requirements
Must have
• encyclopedia style large size book
must look professional and expensive

Nice to have
• - gold-color hardcover, or some gold-color elements
- some simple and decent graphic element (e.g. an ancient column, or some other architectural detail), if any
Should not have
• no color-pictures
no author's name

```html
<!DOCTYPE html>
<html lang="de">
<head>
<meta charset="utf-8">
<title>Azurne Laterne – Buchumschlag</title>
<link rel="stylesheet" href="https://fonts.googleapis.com/css2?family=Tenor+Sans&family=Cinzel:wght@500;600;700&display=swap">
<style>
  :root {
    --page: #ffffff;
    --suit-dark: #141414;
    --suit-mid: #222222;
    --backdrop: #7a7a7a;
    --gold: #ffd200;
    --gold-edge: #b98f00;
    --ink-light: #f4f4f4;
    --rule: #d8d8d8;
  }
  html, body {
    margin: 0;
    padding: 0;
    width: 1000px;
    height: 1200px;
    overflow: hidden;
    background: var(--page);
  }
  .canvas {
    position: relative;
    width: 1000px;
    height: 1200px;
  }
  .cover {
    position: absolute;
    left: 166px;
    top: 74px;
    width: 698px;
    height: 1048px;
    overflow: hidden;
    background: var(--suit-dark);
    box-shadow: 2px 3px 6px rgba(0,0,0,0.35);
  }
  .cover-photo {
    position: absolute;
    inset: 0;
    background:
      radial-gradient(ellipse 18% 30% at 50% 22%, rgba(235,235,235,0.55), rgba(235,235,235,0) 100%),
      linear-gradient(180deg, var(--backdrop) 0%, #5a5a5a 10%, var(--suit-mid) 22%, var(--suit-dark) 60%, #101010 100%);
  }
  .title {
    position: absolute;
    left: 0;
    right: 0;
    top: 524px;
    margin: 0;
    text-align: center;
    font-family: "Tenor Sans", sans-serif;
    font-weight: 400;
    color: var(--gold);
    line-height: 1;
    -webkit-text-stroke: 4px var(--gold);
    text-shadow: 1px 1px 0 var(--gold-edge), 2px 3px 0 var(--gold-edge), 3px 5px 5px rgba(0,0,0,0.75);
  }
  .title-line {
    display: block;
  }
  .title-line--first {
    font-size: 124px;
    letter-spacing: 0;
  }
  .title-line--second {
    font-size: 130px;
    letter-spacing: 0;
    margin-top: 8px;
  }
  .subtitle {
    position: absolute;
    left: 0;
    right: 0;
    top: 828px;
    margin: 0;
    text-align: center;
    font-family: "Cinzel", serif;
    font-weight: 700;
    color: var(--ink-light);
    font-size: 27px;
    line-height: 31px;
  }
  .rule {
    position: absolute;
    left: 208px;
    width: 296px;
    top: 937px;
    height: 3px;
    background: var(--rule);
  }
  .region {
    position: absolute;
    left: 0;
    right: 0;
    top: 958px;
    margin: 0;
    text-align: center;
    font-family: "Cinzel", serif;
    font-weight: 700;
    color: var(--ink-light);
    font-size: 18px;
  }
</style>
</head>
<body>
  <div class="canvas">
    <div class="cover">
      <div class="cover-photo" role="img" aria-label="Schwarzweiß-Foto: Oberkörper eines Mannes im dunklen Nadelstreifenanzug mit weißem Hemd und schwarzer Krawatte vor grauem Hintergrund"></div>
      <h1 class="title">
        <span class="title-line title-line--first">AZURNE</span>
        <span class="title-line title-line--second">LATERNE</span>
      </h1>
      <p class="subtitle">
        DER BEDEUTENDSTEN<br>
        Gründer und Vordenker<br>
        Norddeutschlands 2016
      </p>
      <div class="rule"></div>
      <p class="region">HAMBURG UND UMLAND</p>
    </div>
  </div>
</body>
</html>
```